Business card

We need a business card design for our company based in Auckland , New Zealand called 'Ridge + Studio Ltd'. We provide architectural services. We would like to see designs that use the max. three colours (such as white, black, grey) The final design should communicate financial safety and growth."
Also I will provide our company logo. I would like to the logo to be embeded onto our business card.

Target Market(s)

new residential house, alteration & addition & light commericila design & drafting service

Industry/Entity Type

Architecture

Contact Information for Business Card

Company name: ridge + studio Ltd.
Name: Mark Delford
Job title: architectural designer & Design LBP
email address: mark@rplusd.co.nz
mobile number: 02 5163 2290
web site: www.rplusd.co.nz

Requirements
Must have
• My project must have..
• - embeded logo (attached company logo)
• I don't have a bigger version for our company logo, but I have one old one, so you can remove the word from it)
• - insert the attached small BKTW logo & LBP logo
• - creative, simple and clear business card.
• - Max. three colours
Nice to have
• - Here are the samples I would like to share with you: http://www.plimvora.com/blog/minimalistic-business-card-designs/
• I would like to have my business card like one of the creation.
Should not have
• TBA

```html
<!DOCTYPE html>
<html lang="en">
<head>
<meta charset="utf-8">
<title>Ridge + Studio Ltd — Business Card</title>
<link href="https://fonts.googleapis.com/css2?family=PT+Sans:wght@400;700&family=PT+Sans+Narrow:wght@400&display=swap" rel="stylesheet">
<style>
  :root {
    --backdrop: #4a4a4a;
    --paper: #ffffff;
    --ink: #141414;
    --grey: #8b8e8e;
    --grey-dark: #555757;
    --text: #2a2a2a;
  }
  * { margin: 0; padding: 0; box-sizing: border-box; }
  html, body {
    width: 1105px; height: 1200px; overflow: hidden;
    background: var(--backdrop);
    font-family: "PT Sans", sans-serif;
  }
  .card {
    position: absolute; left: 193px;
    width: 720px; height: 411px;
    background: var(--paper);
    overflow: hidden;
  }
  .card--front { top: 167px; }
  .card--back { top: 623px; }

  .person-name {
    position: absolute; left: 61px; top: 76px;
    font-size: 24px; font-weight: 700; letter-spacing: 0.5px;
    color: var(--ink);
  }
  .person-role {
    position: absolute; left: 61px; top: 112px;
    font-family: "PT Sans Narrow", sans-serif;
    font-size: 19px; line-height: 28px; color: var(--grey);
  }
  .company-name {
    position: absolute; left: 61px; top: 182px;
    font-size: 19px; color: var(--text);
  }
  .contact-list {
    position: absolute; left: 61px; top: 218px;
    list-style: none;
  }
  .contact-item {
    display: flex; align-items: center; gap: 12px;
    height: 27px; font-size: 19px; color: var(--text);
  }
  .contact-icon { width: 16px; height: 16px; flex: none; }

  .brand {
    position: absolute; left: 430px; top: 170px;
    display: flex; align-items: center; gap: 16px;
  }
  .brand-dot { width: 44px; height: 44px; border-radius: 50%; background: var(--ink); }
  .brand-name { font-size: 30px; font-weight: 700; color: var(--ink); }

  .footer-band {
    position: absolute; left: 0; top: 350px;
    width: 720px; height: 61px;
    background: linear-gradient(to bottom, var(--grey) 0%, var(--grey-dark) 35%, var(--ink) 70%);
  }

  .partner-row {
    position: absolute; left: 0; top: 131px; width: 720px; height: 151px;
  }
  .partner-badge {
    position: absolute; left: 187px; top: 5px;
    width: 140px; height: 140px; border-radius: 50%;
    background: var(--ink);
  }
  .partner-divider {
    position: absolute; left: 336px; top: 0;
    width: 2px; height: 151px; background: var(--grey);
  }
  .partner-name {
    position: absolute; left: 352px; top: 44px;
    font-size: 56px; font-weight: 700; line-height: 1;
    color: var(--grey-dark);
  }
  .back-website {
    position: absolute; left: 0; top: 346px; width: 720px;
    text-align: center; font-size: 19px; color: var(--grey-dark);
  }
</style>
</head>
<body>

<section class="card card--front">
  <h1 class="person-name">MARK DELFORD</h1>
  <p class="person-role">architectural designer<br>&amp; Design LBP</p>
  <p class="company-name">Ridge + Studio Ltd.</p>
  <ul class="contact-list">
    <li class="contact-item">
      <svg class="contact-icon" viewBox="0 0 16 16"><rect x="4" y="1" width="8" height="14" rx="1.5" fill="none" stroke="var(--ink)" stroke-width="2"/><rect x="7" y="11.5" width="2" height="1.5" fill="var(--ink)"/></svg>
      02 5163 2290
    </li>
    <li class="contact-item">
      <svg class="contact-icon" viewBox="0 0 16 16"><rect x="1" y="4" width="14" height="9" fill="var(--ink)"/><path d="M1 4 L8 9.5 L15 4" fill="none" stroke="var(--paper)" stroke-width="1.3"/></svg>
      mark@rplusd.co.nz
    </li>
    <li class="contact-item">
      <svg class="contact-icon" viewBox="0 0 16 16"><circle cx="8" cy="8" r="7" fill="var(--ink)"/><path d="M1 8 H15 M8 1 C4 5 4 11 8 15 M8 1 C12 5 12 11 8 15" fill="none" stroke="var(--paper)" stroke-width="1"/></svg>
      www.rplusd.co.nz
    </li>
  </ul>

  <div class="brand">
    <span class="brand-dot"></span>
    <span class="brand-name">ridge + studio</span>
  </div>

  <div class="footer-band" role="img" aria-label="Decorative grey and black footer band"></div>
</section>

<section class="card card--back">
  <div class="partner-row">
    <div class="partner-badge" role="img" aria-label="Partner certification badge"></div>
    <div class="partner-divider"></div>
    <div class="partner-name">BKTW</div>
  </div>
  <p class="back-website">www.rplusd.co.nz</p>
</section>

</body>
</html>
```